Business Card Design Project - 2 sided

We need a business card design for a card having one business on each side (ie. two businesses on one card). Would like a design that incorporates logo, tagline and normal fields (name, position, address, phone).

Would also like an allowance for small font text along the bottom (text to be determined, but less than 50 characters).

NB. Attached logo for Harbor Quill has two variations - either can be used.

www.harborquill-example.com / www.velmaro-example.com

```html
<!DOCTYPE html>
<html lang="en">
<head>
<meta charset="utf-8">
<title>Harbor Quill / Velmaro – Business Card</title>
<link href="https://fonts.googleapis.com/css2?family=Open+Sans:wght@400;600;700&display=swap" rel="stylesheet">
<style>
  :root{
    --stage:#ece8e3;
    --card:#ffffff;
    --green:#8cc63f;
    --green-light:#a3cf5a;
    --green-dark:#6da53a;
    --navy:#2b2a6b;
    --blue:#1f7fb8;
    --blue-light:#4aa6d8;
    --ink:#222222;
    --muted:#3d6f8f;
    --white:#ffffff;
  }
  *{box-sizing:border-box;margin:0;padding:0}
  html,body{width:1200px;height:402px;overflow:hidden}
  body{background:var(--stage);font-family:"Open Sans",Arial,sans-serif;position:relative}
  .card{position:absolute;top:56px;width:511px;height:292px;border-radius:14px;background:var(--card);overflow:hidden;box-shadow:0 2px 6px rgba(0,0,0,.25)}
  .card--harbor{left:62px}
  .card--velmaro{left:626px}
  .card__shape{position:absolute;inset:0;width:511px;height:292px}
  .brand{position:absolute;text-align:center}
  .card--harbor .brand{left:0;width:250px;top:126px}
  .card--velmaro .brand{left:0;width:240px;top:112px}
  .brand__name{display:flex;align-items:center;justify-content:center;gap:8px;font-weight:600;letter-spacing:1px}
  .card--harbor .brand__name{font-size:19px;color:var(--navy);text-transform:uppercase}
  .card--velmaro .brand__name{font-size:34px;color:var(--blue);letter-spacing:0;line-height:1}
  .brand__dot{display:inline-block;border-radius:50%}
  .card--harbor .brand__dot{width:12px;height:12px;background:var(--green)}
  .card--velmaro .brand__dot{width:26px;height:26px;background:var(--green)}
  .brand__tagline{margin-top:6px;font-size:9px;font-weight:600;color:var(--ink);white-space:nowrap}
  .card--velmaro .brand__tagline{font-size:10.5px;font-weight:400;color:var(--muted);margin-top:4px;padding-left:40px}
  .details{position:absolute;left:304px;top:44px;color:var(--white)}
  .card--velmaro .details{left:304px}
  .details__name{font-size:16px;font-weight:700;line-height:22px}
  .details__title{font-size:12px;font-weight:400}
  .contacts{list-style:none;margin-top:9px}
  .contacts li{display:flex;align-items:center;gap:4px;font-size:12px;line-height:17.2px}
  .contacts svg{width:9px;height:9px;flex:none}
  .address{margin-top:10px;font-size:12px;line-height:17px}
  .footnote{margin-top:13px;font-size:9px;line-height:14px;letter-spacing:.2px}
</style>
</head>
<body>

<section class="card card--harbor">
  <svg class="card__shape" viewBox="0 0 511 292" aria-hidden="true">
    <path d="M232 0 C262 60 268 150 236 292 L511 292 L511 0 Z" fill="var(--green)"/>
    <path d="M222 0 C252 60 256 150 214 292 L236 292 C268 150 262 60 232 0 Z" fill="var(--navy)"/>
    <path d="M226 0 C255 62 258 150 222 292" fill="none" stroke="var(--white)" stroke-width="1.6"/>
  </svg>
  <div class="brand">
    <div class="brand__name"><span class="brand__dot"></span>Harbor Quill</div>
    <div class="brand__tagline">Website Translation and Localisation Specialist...</div>
  </div>
  <div class="details">
    <div class="details__name">Your Name <span class="details__title">/ Title</span></div>
    <ul class="contacts">
      <li><svg viewBox="0 0 10 10"><path d="M2 1h2l1 2-1 1c1 1 1 2 2 2l1-1 2 1v2C6 8 2 4 2 1z" fill="currentColor"/></svg>123-456-7890</li>
      <li><svg viewBox="0 0 10 10"><rect x="3" y="0.5" width="4.5" height="9" rx="1" fill="currentColor"/></svg>123-456-7890</li>
      <li><svg viewBox="0 0 10 10"><rect x="1" y="4" width="8" height="5" rx="1" fill="currentColor"/><path d="M1 4c1-3 7-3 8 0" fill="none" stroke="currentColor" stroke-width="1.4"/></svg>123-456-7890</li>
      <li><svg viewBox="0 0 10 10"><rect x="0.5" y="2" width="9" height="6.5" rx="1" fill="currentColor"/></svg>name@website.com</li>
      <li><svg viewBox="0 0 10 10"><circle cx="5" cy="5" r="4.3" fill="currentColor"/></svg>www.website.com</li>
    </ul>
    <p class="address">Complex name, Street name<br>City, State, zip code</p>
    <p class="footnote">xxxxxxxxxxxxxxxxxxxxxxxxxxx<br>xxxxxxxxxxxxxxxxxxxxxxxxxxx</p>
  </div>
</section>

<section class="card card--velmaro">
  <svg class="card__shape" viewBox="0 0 511 292" aria-hidden="true">
    <defs>
      <linearGradient id="velmaroGreen" x1="0" x2="1" y1="0" y2="0">
        <stop offset="0" stop-color="var(--green-light)"/>
        <stop offset="1" stop-color="var(--green-dark)"/>
      </linearGradient>
      <linearGradient id="velmaroBlue" x1="0" x2="1" y1="0" y2="0">
        <stop offset="0" stop-color="var(--blue)"/>
        <stop offset="1" stop-color="var(--blue-light)"/>
      </linearGradient>
    </defs>
    <path d="M248 0 C270 70 268 170 234 292 L511 292 L511 0 Z" fill="url(#velmaroGreen)"/>
    <path d="M226 0 C256 62 258 150 214 292 L236 292 C268 170 270 70 248 0 Z" fill="url(#velmaroBlue)"/>
    <path d="M233 0 C262 64 262 152 222 292" fill="none" stroke="var(--white)" stroke-width="1.6"/>
  </svg>
  <div class="brand">
    <div class="brand__name"><span class="brand__dot"></span>Velmaro LLC</div>
    <div class="brand__tagline">Professional SEO Services</div>
  </div>
  <div class="details">
    <div class="details__name">Your Name <span class="details__title">/ Title</span></div>
    <ul class="contacts">
      <li><svg viewBox="0 0 10 10"><path d="M2 1h2l1 2-1 1c1 1 1 2 2 2l1-1 2 1v2C6 8 2 4 2 1z" fill="currentColor"/></svg>123-456-7890</li>
      <li><svg viewBox="0 0 10 10"><rect x="3" y="0.5" width="4.5" height="9" rx="1" fill="currentColor"/></svg>123-456-7890</li>
      <li><svg viewBox="0 0 10 10"><rect x="1" y="4" width="8" height="5" rx="1" fill="currentColor"/><path d="M1 4c1-3 7-3 8 0" fill="none" stroke="currentColor" stroke-width="1.4"/></svg>123-456-7890</li>
      <li><svg viewBox="0 0 10 10"><rect x="0.5" y="2" width="9" height="6.5" rx="1" fill="currentColor"/></svg>name@website.com</li>
      <li><svg viewBox="0 0 10 10"><circle cx="5" cy="5" r="4.3" fill="currentColor"/></svg>www.website.com</li>
    </ul>
    <p class="address">Complex name, Street name<br>City, State, zip code</p>
    <p class="footnote">xxxxxxxxxxxxxxxxxxxxxxxxxxx<br>xxxxxxxxxxxxxxxxxxxxxxxxxxx</p>
  </div>
</section>

</body>
</html>
```